Oil and Gas Exploration and Production company needs a business card design

We need a business card design using our logo and colors in the logo. We want a mainstream design.

```html
<!DOCTYPE html>
<html lang="en">
<head>
<meta charset="utf-8">
<title>Solara Oil &amp; Gas – Business Card</title>
<link rel="stylesheet" href="https://fonts.googleapis.com/css2?family=Open+Sans:wght@400;600;700&display=swap">
<style>
  :root {
    --ink: #111111;
    --gold: #c3952b;
    --paper: #f4f4f2;
    --mist: #e9e8e3;
    --stage: #2b2b2b;
    --text: #1c1c1c;
  }
  * { box-sizing: border-box; margin: 0; padding: 0; }
  html, body {
    width: 1200px; height: 922px; overflow: hidden;
    background: var(--stage);
    font-family: "Open Sans", Arial, sans-serif;
  }
  .sheet {
    width: 1200px; height: 922px;
    display: flex; flex-direction: column; align-items: center; justify-content: center;
    gap: 40px;
  }
  .card {
    position: relative;
    width: 700px; height: 400px;
    background: var(--paper);
    overflow: hidden;
    box-shadow: 0 8px 24px rgba(0,0,0,.35);
  }
  .brand {
    display: flex; align-items: center; gap: 14px;
    font-weight: 700; color: var(--ink);
  }
  .brand-dot {
    border-radius: 50%; background: var(--gold); flex: none;
  }
  /* Front */
  .front .halo {
    position: absolute; right: -70px; top: -60px;
    width: 380px; height: 380px; border-radius: 50%;
    background: var(--mist);
  }
  .front .brand { position: absolute; left: 48px; top: 58px; font-size: 40px; }
  .front .brand-dot { width: 30px; height: 30px; }
  .person { position: absolute; left: 48px; top: 152px; }
  .person-name { font-size: 24px; font-weight: 600; color: var(--ink); }
  .person-role { font-size: 17px; color: var(--gold); margin-top: 2px; }
  .contact { position: absolute; left: 48px; top: 230px; list-style: none; }
  .contact li {
    display: flex; align-items: center; gap: 10px;
    font-size: 16px; color: var(--text); line-height: 25px;
  }
  .contact svg { width: 16px; height: 16px; flex: none; }
  .bands { position: absolute; left: 0; bottom: 0; width: 700px; height: 60px; }
  /* Back */
  .back .shade {
    position: absolute; left: -90px; bottom: -150px;
    width: 360px; height: 360px; border-radius: 50%;
    background: #cfcfcd;
  }
  .back .brand {
    position: absolute; left: 0; right: 0; top: 170px; justify-content: center;
    font-size: 52px;
  }
  .back .brand-dot { width: 40px; height: 40px; }
</style>
</head>
<body>
<main class="sheet">
  <section class="card front">
    <div class="halo"></div>
    <div class="brand"><span class="brand-dot"></span>Solara Oil &amp; Gas</div>
    <div class="person">
      <div class="person-name">Dale Whitmore</div>
      <div class="person-role">CEO</div>
    </div>
    <ul class="contact">
      <li><svg viewBox="0 0 16 16"><rect width="16" height="16" rx="3" fill="#c3952b"/><rect x="4" y="5" width="8" height="7" rx="1" fill="#fff"/><rect x="5" y="3" width="6" height="3" fill="#fff"/></svg>1 817-555-0142</li>
      <li><svg viewBox="0 0 16 16"><rect width="16" height="16" rx="3" fill="#c3952b"/><path d="M5 3.5l2 2-1 1.5c.8 1.6 1.8 2.6 3.4 3.4l1.5-1 2 2-1.4 1.6C8 12.7 3.3 8 3.5 4.9z" fill="#fff"/></svg>+1 817-555-0178</li>
      <li><svg viewBox="0 0 16 16"><rect width="16" height="16" rx="3" fill="#c3952b"/><rect x="3" y="4.5" width="10" height="7" fill="#fff"/><path d="M3 4.5l5 4 5-4" stroke="#c3952b" fill="none"/></svg>info@solaraoilgas.com</li>
      <li><svg viewBox="0 0 16 16"><rect width="16" height="16" rx="3" fill="#c3952b"/><path d="M8 2.5a3.5 3.5 0 0 1 3.5 3.5C11.5 9 8 13.5 8 13.5S4.5 9 4.5 6A3.5 3.5 0 0 1 8 2.5z" fill="#fff"/><circle cx="8" cy="6" r="1.3" fill="#c3952b"/></svg>PO Box 4410, Fort Worth, TX 76101-4410, USA</li>
    </ul>
    <svg class="bands" viewBox="0 0 700 60" preserveAspectRatio="none">
      <polygon points="300,60 340,22 700,22 700,60" fill="#111111"/>
      <polygon points="0,60 0,42 320,42 302,60" fill="#c3952b"/>
    </svg>
  </section>

  <section class="card back">
    <div class="shade"></div>
    <div class="brand"><span class="brand-dot"></span>Solara Oil &amp; Gas</div>
  </section>
</main>
</body>
</html>
```